Business Card Design needed - Something Awesome!

Need a business card designed. Company is "Marlowe Advisory" we do consulting and also have sales automation technology.
I'm going to use thick stock or metal, something really nice... I was thinking about a QR Code on the back that would just upload my contact info to the persons contact, etc -

This is a Strategy Company with a tech feel. I'm open to ideas but really want this to be nice!

I need a template that should include:

Name | Position or Title
D: 415.902.3376
www.marloweadvisory.example

I'm going to attach my contact so you can use that one, I need to get this printed.

Target Market(s)

Small to mid size customers, Entrepreneurs etc.

Industry/Entity Type

Consulting, Tech, Private Equity.

Contact Information for Business Card

Name, Phone, Maybe email, URL

Font styles to use
Sans Serif

Colors

Designer to choose only greyscale colors for use in the design.

Requirements
Must have
• Fresh, Clean, stand out from the crowd - will be on thick stock or metal.
Nice to have
• Clean, simple yet impactful.
Should not have
• Not cartoonish

```html
<!DOCTYPE html>
<html lang="en">
<head>
<meta charset="utf-8">
<title>Marlowe Advisory — Business Card</title>
<link href="https://fonts.googleapis.com/css2?family=Roboto:wght@400;700&display=swap" rel="stylesheet">
<style>
  :root {
    --backdrop: #3b3b3b;
    --card: #0e0e0e;
    --silver: #c8c8c8;
    --silver-dim: #a9a9a9;
    --divider: #6a6a6a;
  }
  * { margin: 0; padding: 0; box-sizing: border-box; }
  html, body {
    width: 1200px; height: 801px; overflow: hidden;
    background: var(--backdrop);
    font-family: 'Roboto', Arial, sans-serif;
  }
  .sheet {
    width: 1200px; height: 801px;
    display: flex; align-items: center; justify-content: center; gap: 48px;
  }
  .card {
    width: 525px; height: 300px;
    background: var(--card);
    position: relative;
    box-shadow: 0 10px 24px rgba(0,0,0,0.35);
  }
  .wordmark {
    color: var(--silver);
    font-weight: 400;
    letter-spacing: 2px;
    display: flex; align-items: center; gap: 10px;
  }
  .wordmark .mark-square {
    width: 14px; height: 14px; background: var(--silver);
  }
  .card-front .wordmark {
    position: absolute; top: 78px; left: 0; right: 0;
    justify-content: center;
    font-size: 50px;
  }
  .contact-row {
    position: absolute; top: 178px; left: 0; right: 0;
    display: flex; justify-content: center; align-items: center;
  }
  .identity { text-align: right; padding-right: 18px; }
  .identity .person {
    color: var(--silver); font-weight: 700; font-size: 15px; letter-spacing: 0.5px;
  }
  .identity .role { color: var(--silver-dim); font-size: 13px; margin-top: 3px; }
  .rule { width: 1px; height: 54px; background: var(--divider); }
  .details { list-style: none; padding-left: 18px; }
  .details li {
    color: var(--silver-dim); font-size: 12.5px; line-height: 18px;
    display: flex; align-items: center; gap: 7px;
  }
  .details svg { width: 10px; height: 10px; fill: var(--silver-dim); flex: none; }
  .card-back { display: flex; align-items: center; justify-content: center; }
  .card-back .wordmark { font-size: 56px; }
</style>
</head>
<body>
<main class="sheet">
  <section class="card card-front" aria-label="Card front">
    <div class="wordmark"><span>MARLOWE</span><span class="mark-square"></span></div>
    <div class="contact-row">
      <div class="identity">
        <p class="person">DORIAN K. VALE</p>
        <p class="role">Founder / CEO</p>
      </div>
      <div class="rule"></div>
      <ul class="details">
        <li><svg viewBox="0 0 10 10"><path d="M2 0.5l2 2-1 1.2c.6 1.3 1.6 2.3 2.9 2.9L7 5.6l2.5 2-1 1.8C4.5 9.5.5 5.5.5 1.5z"/></svg>415.902.3376</li>
        <li><svg viewBox="0 0 10 10"><path d="M0 2h10v6H0zM0 2l5 3.5L10 2" stroke="#0e0e0e" stroke-width="0.8"/></svg>info@marloweadvisory.example</li>
        <li><svg viewBox="0 0 10 10"><circle cx="5" cy="5" r="4.5"/><path d="M0.5 5h9M5 0.5c-2.5 3-2.5 6 0 9M5 0.5c2.5 3 2.5 6 0 9" stroke="#0e0e0e" stroke-width="0.7" fill="none"/></svg>www.marloweadvisory.example</li>
      </ul>
    </div>
  </section>
  <section class="card card-back" aria-label="Card back">
    <div class="wordmark"><span>MARLOWE</span><span class="mark-square"></span></div>
  </section>
</main>
</body>
</html>
```